Informational Site for Advanced Chemistry R&D

The company develops oxidation chemistry for air, water, fuel pollution controls. The site has been prototyped at www.velquaresearch.example. Take a look. Now, the task is to design it for eye-catching beauty with use of color, on-page scroll-driven color transition and parallax effects. Should capture the themes: high technology, wow it's beautiful, modern, uncluttered, clean urban environment.

Target Market(s)

China Environmentally Conscious Government and Industry,

Industry/Entity Type

It Company

Number of Pages Required

3 page

Font styles to use
Sans Serif

Requirements
Must have
• Parallax effects, desktop compatible, Rich, Modern, Simple, Graphic
Nice to have
• Mobile Phone Compatible
Should not have
• Flash, or anything that is slow to load or requires high bandwidth

```html
<!DOCTYPE html>
<html lang="en">
<head>
<meta charset="utf-8">
<title>Velquara – Advanced Oxidation Science</title>
<link href="https://fonts.googleapis.com/css2?family=Open+Sans:wght@400;600;700&display=swap" rel="stylesheet">
<style>
:root{
  --ink:#1d1d1d;
  --nav:#1b1c1e;
  --accent:#2bb7c9;
  --blue:#1f73c4;
  --blue-deep:#145ea8;
  --title-blue:#1e6fb8;
  --navy:#0e1a33;
  --grey-text:#8a8f96;
  --line:#e4e6ea;
  --partner-bg:#e9edf1;
  --footer:#151618;
  --white:#ffffff;
}
*{box-sizing:border-box;margin:0;padding:0}
html,body{width:1200px;height:3982px;overflow:hidden}
body{font-family:"Open Sans",Arial,sans-serif;color:var(--ink);background:#fff;position:relative}
section,header,footer{position:absolute;left:0;width:1200px;overflow:hidden}

/* nav */
.site-nav{top:0;height:75px;background:var(--nav)}
.brand-dot{position:absolute;left:108px;top:20px;width:36px;height:36px;border-radius:50%;background:var(--accent)}
.menu{position:absolute;right:110px;top:0;height:75px;display:flex;gap:44px;align-items:center;list-style:none}
.menu li{font-size:13px;color:#e4e4e4;letter-spacing:.3px}
.menu li.active{color:var(--accent)}

/* hero */
.hero{top:75px;height:530px;background:linear-gradient(180deg,#6f5a3e 0%,#a98b60 35%,#5e4a34 65%,#231a13 100%)}
.hero-brand{position:absolute;left:0;width:1200px;top:130px;text-align:center;color:#fff}
.hero-brand .mark{display:inline-block;width:62px;height:62px;border-radius:50%;background:#fff;margin-bottom:10px}
.hero-brand .name{font-size:40px;font-weight:700;letter-spacing:1px}
.hero-title{position:absolute;left:0;width:1200px;top:290px;text-align:center;color:#fff;font-size:31px;font-weight:600;line-height:1.3;text-shadow:0 2px 6px rgba(0,0,0,.4)}
.hero-arrow{position:absolute;top:250px}
.scroll-cue{position:absolute;left:0;width:1200px;top:465px;text-align:center;color:#fff;font-size:11px;letter-spacing:1px}

/* intro */
.intro{top:605px;height:523px;background:linear-gradient(180deg,#2585d6 0%,var(--blue) 60%,var(--blue-deep) 100%);color:#fff;text-align:center}
.section-title{font-size:26px;font-weight:600;letter-spacing:.5px}
.wave{display:block;margin:8px auto 0}
.intro .section-title{margin-top:42px}
.intro .lead{width:960px;margin:22px auto 0;font-size:12px;line-height:22px;color:#e3efff}
.pillars{position:absolute;top:230px;left:112px;width:976px;display:flex;justify-content:space-between}
.pillar{width:290px}
.pillar h3{font-size:19px;font-weight:600;margin:10px 0 8px}
.pillar p{font-size:12px;line-height:21px;color:#e3efff}

/* features */
.features{top:1128px;height:725px;background:#fff}
.feature-row{position:absolute;left:112px;width:976px;display:flex;justify-content:space-between}
.feature{width:290px;text-align:center}
.feature .photo{width:140px;height:140px;border-radius:50%;margin:0 auto;border:5px solid #eef0f3}
.feature h3{font-size:19px;font-weight:600;color:var(--title-blue);margin:22px 0 8px;letter-spacing:.3px}
.feature p{font-size:12px;line-height:21px;color:var(--grey-text)}
.feature-divider{position:absolute;left:112px;width:976px;top:362px;height:1px;background:var(--line)}

/* oxidation band */
.oxidation{top:1853px;height:407px}
.ox-panel{position:absolute;left:0;top:0;width:672px;height:407px;background:linear-gradient(135deg,#142447,var(--navy));color:#fff;padding:60px 0 0 118px}
.ox-panel h2{font-size:26px;font-weight:600;margin-bottom:20px}
.ox-panel p{font-size:12.5px;line-height:24px;width:500px;color:#dfe6f3}
.ox-list{list-style:none;margin:10px 0 12px}
.ox-list li{font-size:13px;line-height:30px;display:flex;align-items:center;gap:8px}
.ox-photo{position:absolute;left:672px;top:0;width:528px;height:407px;background:linear-gradient(180deg,#1c2f6a 0%,#2b4a8f 50%,#0d1430 70%,#1a2750 100%)}
.ox-button{position:absolute;left:685px;top:340px;width:515px;height:67px;background:var(--blue);color:#fff;font-size:20px;display:flex;align-items:center;padding-left:22px;gap:12px}

/* solutions */
.solutions{top:2260px;height:1020px;background:#fff}
.solutions .section-title{text-align:center;margin-top:40px;color:#2a2a2a}
.solution{position:absolute;width:465px}
.solution h3{font-size:19px;font-weight:600;color:#222;margin-bottom:16px}
.solution .photo{width:465px;height:200px}
.solution p{font-size:12px;line-height:21px;color:var(--grey-text);margin:22px 0 18px}
.btn{display:inline-flex;align-items:center;gap:6px;background:var(--blue);color:#fff;font-size:12px;font-weight:700;padding:14px 20px;border-radius:4px}

/* partners */
.partners{top:3280px;height:286px;background:var(--partner-bg);text-align:center}
.partners .section-title{margin-top:30px;color:#2a2a2a}
.partner-row{position:absolute;top:120px;left:230px;width:740px;display:flex;justify-content:space-between;align-items:center}
.partner-badge{width:120px;height:120px;display:flex;align-items:center;justify-content:center}
.partner-name{font-size:17px;font-weight:600;color:#1a8fb5}
.partner-feature{width:165px;height:130px;background:#3d4450;color:#fff;font-size:15px;line-height:22px;display:flex;align-items:center;justify-content:center;text-align:center;border-radius:3px}
.seal{width:100px;height:100px;border-radius:50%}

/* contact */
.contact{top:3566px;height:310px}
.map{position:absolute;left:0;top:0;width:600px;height:310px;background:linear-gradient(135deg,#dfe2e6,#c8ccd2)}
.city{position:absolute;left:600px;top:0;width:600px;height:310px;background:linear-gradient(180deg,#4a6280 0%,#2d3e55 60%,#1c2637 100%)}
.contact-circle{position:absolute;left:430px;top:-10px;width:330px;height:330px;border-radius:50%;background:rgba(22,110,200,.92);border:4px solid rgba(255,255,255,.85);color:#fff;padding:80px 0 0 68px}
.contact-circle .row{display:flex;gap:12px;font-size:11.5px;line-height:18px;margin-bottom:14px}
.contact-circle hr{border:0;border-top:1px solid rgba(255,255,255,.5);width:190px;margin:0 0 14px 26px}
.pin-marker{position:absolute;left:270px;top:95px}
.invite{position:absolute;left:768px;top:75px;width:330px;color:#fff;font-size:17px;line-height:28px}
.invite .btn{margin-top:16px;padding:13px 30px;font-size:13px}

/* footer */
.site-footer{top:3876px;height:106px;background:var(--footer)}
.copyright{position:absolute;left:112px;top:42px;font-size:11px;color:#9b9b9b}
.social{position:absolute;right:100px;top:35px;display:flex;gap:12px}
.social span{width:34px;height:34px;border-radius:50%;background:#3a3c40}
.social span.on{background:var(--accent)}
</style>
</head>
<body>

<header class="site-nav">
  <span class="brand-dot"></span>
  <ul class="menu">
    <li class="active">HOME</li><li>TECHNOLOGY</li><li>PRODUCTS</li><li>ABOUT US</li><li>CONTACT</li>
  </ul>
</header>

<section class="hero" role="img" aria-label="Industrial skyline with smoke stacks under a smoky sunset sky">
  <svg class="hero-arrow" style="left:28px" width="20" height="36" viewBox="0 0 20 36"><path d="M16 2 L4 18 L16 34" fill="none" stroke="rgba(255,255,255,.7)" stroke-width="2"/></svg>
  <svg class="hero-arrow" style="right:28px" width="20" height="36" viewBox="0 0 20 36"><path d="M4 2 L16 18 L4 34" fill="none" stroke="rgba(255,255,255,.7)" stroke-width="2"/></svg>
  <div class="hero-brand">
    <span class="mark"></span>
    <div class="name">Velquara</div>
  </div>
  <h1 class="hero-title">Advanced Oxidation<br>Science for Environmental Pollution Management</h1>
  <div class="scroll-cue">SCROLL<br>
    <svg width="14" height="22" viewBox="0 0 14 22" style="margin-top:6px"><rect x="1" y="1" width="12" height="20" rx="6" fill="none" stroke="#fff" stroke-width="1.5"/><line x1="7" y1="5" x2="7" y2="9" stroke="#fff" stroke-width="1.5"/></svg>
  </div>
</section>

<section class="intro">
  <h2 class="section-title">NEW IDEAS FOR A CLEANER WORLD</h2>
  <svg class="wave" width="46" height="12" viewBox="0 0 46 12"><path d="M2 4 Q12 0 23 4 T44 4 M2 9 Q12 5 23 9 T44 9" fill="none" stroke="#fff" stroke-width="2"/></svg>
  <p class="lead">Our research turns oxidation chemistry into practical tools that clean the air, water and fuel of growing cities. We design compact processes that work at low heat and pressure, use less energy and fit into existing plants, so industry and government can reach cleaner targets faster and at lower cost. Every system is tested in the field before it reaches our partners.</p>
  <div class="pillars">
    <div class="pillar">
      <svg width="50" height="62" viewBox="0 0 50 62"><path d="M25 2 C25 2 4 30 4 40 A21 21 0 0 0 46 40 C46 30 25 2 25 2Z" fill="#fff"/></svg>
      <h3>WATER</h3>
      <p>Oxidation breaks down dissolved organics in process water. Cleaner discharge with a compact unit that fits existing treatment lines.</p>
    </div>
    <div class="pillar">
      <svg width="60" height="62" viewBox="0 0 60 62"><circle cx="30" cy="32" r="28" fill="#fff"/><path d="M18 44 C18 26 30 18 44 18 C44 34 34 44 18 44Z" fill="var(--blue)"/></svg>
      <h3>AIR</h3>
      <p>Stack gases are treated on site so sulfur and nitrogen compounds are captured before they ever reach the open sky.</p>
    </div>
    <div class="pillar">
      <svg width="50" height="62" viewBox="0 0 50 62"><rect x="6" y="6" width="28" height="52" rx="3" fill="#fff"/><rect x="11" y="12" width="18" height="12" fill="var(--blue)"/><path d="M34 20 L42 26 L42 48 A3 3 0 0 0 48 48 L48 22" fill="none" stroke="#fff" stroke-width="3"/></svg>
      <h3>FUEL</h3>
      <p>Low temperature desulfurization delivers cleaner fuel oil at a fraction of the usual plant cost.</p>
    </div>
  </div>
</section>

<section class="features">
  <div class="feature-row" style="top:60px">
    <div class="feature"><div class="photo" role="img" aria-label="Hands holding a young seedling in soil" style="background:linear-gradient(160deg,#9bc27a,#5a6b3c)"></div>
      <h3>ENVIRONMENTAL</h3><p>Processes built around natural chemistry. They leave fewer by-products and need less energy to run each day.</p></div>
    <div class="feature"><div class="photo" role="img" aria-label="Factory chimneys against a blue sky" style="background:linear-gradient(180deg,#5f9fd8,#b9c6cf)"></div>
      <h3>POLLUTION CONTROL</h3><p>Targeted treatment for stacks, tanks and outfalls that meets strict limits without bulky equipment.</p></div>
    <div class="feature"><div class="photo" role="img" aria-label="Engineer inspecting a treatment installation" style="background:linear-gradient(160deg,#8a8f96,#3d4248)"></div>
      <h3>SOLUTIONS EMPLOYING</h3><p>Field proven methods adapted to each site. Our team supports design, startup and long term operation.</p></div>
  </div>
  <div class="feature-divider"></div>
  <div class="feature-row" style="top:410px">
    <div class="feature"><div class="photo" role="img" aria-label="Green leaves and a recycling symbol" style="background:linear-gradient(160deg,#a8d06c,#4f7d2e)"></div>
      <h3>NATURE'S MOST</h3><p>We use the same reactive species nature uses to clean itself, scaled up for modern industry.</p></div>
    <div class="feature"><div class="photo" role="img" aria-label="Fresh green plant close-up" style="background:linear-gradient(160deg,#7fcf86,#2e7a45)"></div>
      <h3>REACTIVE FREE</h3><p>Short lived radicals do the work and then vanish, leaving no harmful residue behind.</p></div>
    <div class="feature"><div class="photo" role="img" aria-label="Small plant inside a glass bulb" style="background:linear-gradient(160deg,#cfe8f7,#5ea6d8)"></div>
      <h3>RADICAL</h3><p>The hydroxyl radical is one of the strongest oxidizers known, fast and highly effective.</p></div>
  </div>
</section>

<section class="oxidation">
  <div class="ox-panel">
    <h2>ADVANCED OXIDATION</h2>
    <p>Advanced Oxidation refers to a variety of techniques employing the Hydroxyl Radical, an energetic, highly reactive cousin of the water molecule:</p>
    <ul class="ox-list">
      <li><svg width="16" height="16" viewBox="0 0 16 16"><circle cx="8" cy="8" r="8" fill="var(--accent)"/><path d="M6 4 L10 8 L6 12" fill="none" stroke="#fff" stroke-width="2"/></svg>To add oxygen to inorganic molecules</li>
      <li><svg width="16" height="16" viewBox="0 0 16 16"><circle cx="8" cy="8" r="8" fill="var(--accent)"/><path d="M6 4 L10 8 L6 12" fill="none" stroke="#fff" stroke-width="2"/></svg>To remove hydrogen from organic molecules</li>
    </ul>
    <p>These transformations convert important industrial contaminants into reactive forms that can be captured or that disintegrate into harmless end products.</p>
  </div>
  <div class="ox-photo" role="img" aria-label="Refinery lit up at night reflected in water"></div>
  <div class="ox-button"><svg width="22" height="22" viewBox="0 0 22 22"><circle cx="11" cy="11" r="10" fill="none" stroke="#fff" stroke-width="2"/><path d="M9 6 L14 11 L9 16" fill="none" stroke="#fff" stroke-width="2"/></svg>LEARN MORE</div>
</section>

<section class="solutions">
  <h2 class="section-title">SOLUTIONS</h2>
  <svg class="wave" width="46" height="12" viewBox="0 0 46 12"><path d="M2 4 Q12 0 23 4 T44 4 M2 9 Q12 5 23 9 T44 9" fill="none" stroke="var(--accent)" stroke-width="2"/></svg>

  <div class="solution" style="left:112px;top:120px">
    <h3>FUEL OIL DESULFURIZATION</h3>
    <div class="photo" role="img" aria-label="Illuminated refinery towers at dusk" style="background:linear-gradient(180deg,#1b3c7a,#2f6fa8 60%,#1a2340)"></div>
    <p>Our proprietary low temperature and pressure advanced oxidation catalytic process reliably removes sulfur from diesel transportation fuel at less than half the operating costs of older hydro desulfurization processes.</p>
    <span class="btn">LEARN MORE ➜</span>
  </div>
  <div class="solution" style="left:623px;top:120px">
    <h3>VOLATILE ORGANIC COMPUNDS (VOC)</h3>
    <div class="photo" role="img" aria-label="Stainless steel processing tanks and pipes" style="background:linear-gradient(135deg,#c9ccd0,#7b8087)"></div>
    <p>Alkanes, alkenes, halogenated hydrocarbons, aromatic hydrocarbons, esters, aldehydes, polycyclic aromatic hydrocarbons. We convert these by products of industrial processes before they enter the atmosphere and cause smog.</p>
    <span class="btn">LEARN MORE ➜</span>
  </div>
  <div class="solution" style="left:112px;top:555px">
    <h3>FLUE GAS SCRUBBING</h3>
    <div class="photo" role="img" aria-label="Smoke stacks against an orange evening sky" style="background:linear-gradient(180deg,#d9853a,#8a4a22 60%,#2a1a12)"></div>
    <p>Desulfurization and denitrification using our proprietary flue gas advanced oxidation catalytic process. Sulfur and nitrogen are oxidized and adsorbed into an environmentally friendly solid medium for safe removal from site.</p>
    <span class="btn">LEARN MORE ➜</span>
  </div>
  <div class="solution" style="left:623px;top:555px">
    <h3>WASTEWATER TREATMENT</h3>
    <div class="photo" role="img" aria-label="Water flowing out of a drainage outlet" style="background:linear-gradient(180deg,#a4b59a,#6d8a7c 55%,#cfd8d4)"></div>
    <p>Photoelectrocatalyzed (PEC) anodic oxidation removes soluble organics. Novel anode design using our proprietary nano carbon surface operates non selectively to remove 99% of contaminants across a wide range of chemical oxygen demand.</p>
    <span class="btn">LEARN MORE ➜</span>
  </div>
</section>

<section class="partners">
  <h2 class="section-title">PARTNERS</h2>
  <svg class="wave" width="46" height="12" viewBox="0 0 46 12"><path d="M2 4 Q12 0 23 4 T44 4 M2 9 Q12 5 23 9 T44 9" fill="none" stroke="var(--accent)" stroke-width="2"/></svg>
  <div class="partner-row">
    <div class="partner-badge"><span class="partner-name">Velquara Systems</span></div>
    <div class="partner-feature">Our Construction<br>Partner in China</div>
    <div class="partner-badge"><span class="seal" style="background:#2a5aa8"></span></div>
    <div class="partner-badge"><span class="seal" style="background:#b0202a"></span></div>
  </div>
</section>

<section class="contact">
  <div class="map" role="img" aria-label="Street map of the office neighbourhood"></div>
  <svg class="pin-marker" width="40" height="54" viewBox="0 0 40 54"><path d="M20 2 A18 18 0 0 1 38 20 C38 34 20 52 20 52 C20 52 2 34 2 20 A18 18 0 0 1 20 2Z" fill="var(--accent)"/><circle cx="20" cy="20" r="7" fill="#fff"/></svg>
  <div class="city" role="img" aria-label="City skyline at dusk"></div>
  <div class="contact-circle">
    <div class="row"><svg width="14" height="18" viewBox="0 0 14 18"><path d="M7 1 A6 6 0 0 1 13 7 C13 12 7 17 7 17 C7 17 1 12 1 7 A6 6 0 0 1 7 1Z" fill="#fff"/></svg><span>Velquara Research Corp.,<br>Harbor Point, Eastvale, U.S.A.</span></div>
    <hr>
    <div class="row"><svg width="14" height="14" viewBox="0 0 14 14"><rect x="1" y="3" width="12" height="9" fill="#fff"/><path d="M1 3 L7 8 L13 3" fill="none" stroke="var(--blue)" stroke-width="1.2"/></svg><span>Mail : info@velquaresearch.example<br>Telephone : +1 555 010 4821</span></div>
  </div>
  <div class="invite">We welcome inquiries regarding the licensing, distribution, and purchase of our products, systems, and technologies.<br><span class="btn">CONTACT NOW</span></div>
</section>

<footer class="site-footer">
  <div class="copyright">© 2016 Velquara. All Rights Reserved.</div>
  <div class="social"><span></span><span></span><span class="on"></span><span></span><span></span></div>
</footer>

</body>
</html>
```